brovlanepass.net

Develop a website for brolanepass.net will be a site to sell tickets for concerts, shows, shows, theaters and others. I need a web design easy view, very easy to use and accumulate events by date. The aim is to develop the site was connected to a complex system that is already developed. (Important this page to a robust system was connected via links the idea is to develop only the front view)
Updates

Reason: I need more designs yet we have not made the decision

Target Market(s)

millennials, adults, who want to enjoy concerts and shows

Industry/Entity Type

Event

Number of Pages Required

5+ page

Colors
1b1b1b
aaaaaa
ffffff

Requirements
Must have
• Easy Vista, accumulation of upcoming events, past events. The tabs should have are: 1 Start: In this part of upcoming events occur. You could put a banner on the top and down the events by date. 2. How to order: page with instructions on how to purchase tickets 3. About Us: The company history 4. Contact: Phones and template for contact by mail 5. Our policies: shopping 6. Notice Privacy: Privacy Notice Copoy 7. Centers Sale: physical places where they can purchase tickets Promoters 8. access: Link to a template
Nice to have
• as you can see p www.quimbarostage.net or farunda.net or farunda.org or gallowmerk.net (important this page to a robust system was connected via links the idea is to develop only the front view)
Should not have
• Many things Tangled

```html
<!DOCTYPE html>
<html lang="en">
<head>
<meta charset="utf-8">
<title>Brovlanepass — Upcoming Events</title>
<link rel="stylesheet" href="https://fonts.googleapis.com/css2?family=Open+Sans:wght@400;600&family=Fredoka:wght@600&family=Caudex:wght@400;700&display=swap">
<style>
  :root {
    --ink: #1b1b1b;
    --black: #000000;
    --grey: #aaaaaa;
    --paper: #ffffff;
    --backdrop: #ececec;
    --line: #d6d6d6;
    --text: #222222;
  }
  * { box-sizing: border-box; margin: 0; padding: 0; }
  html, body { width: 1113px; height: 1200px; overflow: hidden; }
  body {
    background: var(--backdrop);
    font-family: "Open Sans", Arial, sans-serif;
    color: var(--text);
    position: relative;
  }
  .crowd-band {
    position: absolute; left: 0; right: 0; top: 1010px; height: 190px;
    background: linear-gradient(to bottom, rgba(150,150,150,0), #9a9a9a 40%, #8c8c8c);
  }
  .site {
    position: absolute; left: 123px; top: 0; width: 867px; height: 1200px;
    background: #f4f4f4;
    box-shadow: 0 0 6px rgba(0,0,0,.12);
  }
  .masthead { position: relative; height: 95px; }
  .brand {
    position: absolute; left: 29px; top: 27px;
    font-family: "Fredoka", "Open Sans", sans-serif; font-weight: 600;
    font-size: 30px; color: var(--ink); letter-spacing: .3px;
  }
  .social { position: absolute; right: 24px; top: 16px; display: flex; gap: 5px; }
  .social span { width: 26px; height: 26px; border-radius: 50%; background: var(--ink); display: block; }
  .account-links {
    position: absolute; right: 24px; top: 62px; display: flex; gap: 12px;
    font-size: 11px; color: var(--ink); align-items: center;
  }
  .cart { display: flex; align-items: center; gap: 10px; }
  .mainnav, .footnav { display: flex; list-style: none; }
  .mainnav {
    height: 40px; background: linear-gradient(#2a2a2a, var(--black));
    align-items: center; padding-left: 31px;
  }
  .mainnav li, .footnav li { color: var(--paper); font-size: 11px; text-transform: uppercase; }
  .mainnav li { margin-right: 42px; }
  .hero {
    position: absolute; left: 19px; top: 159px; width: 834px; height: 323px;
    background: radial-gradient(ellipse at 60% 55%, #dff1ee 0%, #8fcac4 30%, #2b8d92 60%, #0d4b5a 100%);
    overflow: hidden;
  }
  .hero-mic {
    position: absolute; left: 0; top: 0; width: 160px; height: 323px;
    background: linear-gradient(90deg, #0d2c33, #2aa3b8 60%, #5fc9d4);
    opacity: .85;
  }
  .hero-title {
    position: absolute; left: 0; right: 0; top: 72px; text-align: center;
    font-family: "Caudex", Georgia, serif; font-weight: 700; font-size: 52px; line-height: 1;
    color: #fafafa; text-shadow: 2px 3px 2px rgba(0,0,0,.75);
  }
  .hero-sub {
    position: absolute; left: 0; right: 0; top: 144px; text-align: center;
    font-family: "Caudex", Georgia, serif; font-weight: 400; font-size: 14px; color: #f4f4f4;
    text-shadow: 1px 1px 1px rgba(0,0,0,.7);
  }
  .hero-cta {
    position: absolute; left: 350px; top: 193px; width: 134px; height: 40px;
    background: var(--ink); color: var(--paper); border-radius: 3px;
    font-size: 13px; display: flex; align-items: center; justify-content: center;
    letter-spacing: .5px;
  }
  .dots { position: absolute; left: 394px; top: 287px; display: flex; gap: 6px; }
  .dots span { width: 10px; height: 10px; border-radius: 50%; background: #cfd8da; border: 1px solid #9aa; }
  .dots span:first-child { background: #f4f4f4; }
  .events-heading {
    position: absolute; left: 22px; top: 512px;
    font-size: 22px; font-weight: 600; color: var(--ink); letter-spacing: .4px;
  }
  .search {
    position: absolute; left: 655px; top: 507px; width: 195px; height: 31px;
    background: var(--paper); border: 1px solid var(--line); border-radius: 3px;
    font-size: 10px; font-style: italic; color: #555; padding: 8px 10px;
  }
  .search svg { position: absolute; right: 8px; top: 10px; }
  .events { position: absolute; left: 25px; top: 563px; display: grid;
    grid-template-columns: repeat(4, 196px); column-gap: 15px; row-gap: 21px; }
  .event { background: var(--paper); border: 1px solid var(--line); height: 216px; position: relative; }
  .event-photo { height: 161px; position: relative; }
  .date {
    position: absolute; left: -1px; top: 88px; width: 54px; height: 73px;
    background: var(--black); color: var(--paper); text-align: center; padding-top: 10px;
  }
  .date .month { font-size: 13px; font-weight: 600; display: block; line-height: 1.2; }
  .date .day { font-size: 27px; font-weight: 600; display: block; line-height: 1.1; }
  .event-name {
    position: absolute; left: 15px; top: 178px; font-size: 13px; font-weight: 600;
    color: var(--ink); text-transform: uppercase; letter-spacing: .3px; white-space: nowrap;
  }
  .footer {
    position: absolute; left: 0; top: 1043px; width: 867px; height: 157px;
    background: var(--black); color: var(--paper);
  }
  .footer .social { left: 389px; right: auto; top: 35px; }
  .footer .social span { background: #1a1a1a; border: 1px solid #333; }
  .footnav { position: absolute; left: 80px; top: 88px; }
  .footnav li { margin-right: 42px; }
  .copyright { position: absolute; left: 0; right: 0; top: 121px; text-align: center; font-size: 10.5px; }
</style>
</head>
<body>
<div class="crowd-band"></div>
<div class="site">
  <header class="masthead">
    <div class="brand">Brovlanepass</div>
    <div class="social" aria-label="Social links"><span></span><span></span><span></span></div>
    <div class="account-links">
      <span>My Account</span><span>|</span><span>Help</span><span>|</span>
      <span class="cart">Cart
        <svg width="10" height="9" viewBox="0 0 10 9"><path d="M0 1h2l1.5 5h5L10 2H3" fill="none" stroke="#1b1b1b" stroke-width="1.4"/><circle cx="4" cy="8" r="1" fill="#1b1b1b"/><circle cx="8" cy="8" r="1" fill="#1b1b1b"/></svg>
        0items</span>
    </div>
  </header>
  <ul class="mainnav">
    <li>Home</li><li>How to order</li><li>About us</li><li>Contact us</li>
    <li>Policies</li><li>Privacy</li><li>Center sale</li><li>Access</li>
  </ul>

  <section class="hero" role="img" aria-label="Concert stage with blurred teal lights and a chrome microphone in the foreground">
    <div class="hero-mic"></div>
    <h1 class="hero-title">Your Seat Is Waiting</h1>
    <p class="hero-sub">Neque porro quisquam est qui dolorem ipsum</p>
    <div class="hero-cta">SEE TICKETS</div>
    <div class="dots"><span></span><span></span><span></span></div>
  </section>

  <h2 class="events-heading">UPCOMING EVENTS</h2>
  <div class="search">Search
    <svg width="9" height="9" viewBox="0 0 9 9"><circle cx="3.7" cy="3.7" r="2.8" fill="none" stroke="#888" stroke-width="1"/><path d="M5.8 5.8L8.5 8.5" stroke="#888" stroke-width="1"/></svg>
  </div>

  <div class="events">
    <article class="event">
      <div class="event-photo" role="img" aria-label="Crowd with raised hands at a brightly lit concert" style="background:linear-gradient(#b8a8e8,#6a4a3a 55%,#2a1208)"></div>
      <div class="date"><span class="month">MAR</span><span class="day">17</span></div>
      <h3 class="event-name">Copper Lantern Choir</h3>
    </article>
    <article class="event">
      <div class="event-photo" role="img" aria-label="Stage with red and blue lights" style="background:linear-gradient(#b0102a,#3a1a8a 50%,#101a4a)"></div>
      <div class="date"><span class="month">MAR</span><span class="day">25</span></div>
      <h3 class="event-name">Rowan Tessely</h3>
    </article>
    <article class="event">
      <div class="event-photo" role="img" aria-label="Band on stage under purple spotlights" style="background:linear-gradient(#0c0c1e,#5a3ac8 55%,#1a1040)"></div>
      <div class="date"><span class="month">APR</span><span class="day">15</span></div>
      <h3 class="event-name">Delmar Hollow Band</h3>
    </article>
    <article class="event">
      <div class="event-photo" role="img" aria-label="Performer on a pink lit stage behind a microphone" style="background:linear-gradient(120deg,#3a0a2a,#c8308a 50%,#e8a0c8)"></div>
      <div class="date"><span class="month">APR</span><span class="day">30</span></div>
      <h3 class="event-name">Kairo Vance</h3>
    </article>
    <article class="event">
      <div class="event-photo" role="img" aria-label="Dancers under violet and pink lights" style="background:linear-gradient(#3a2a6a,#c040c8 55%,#2a0a3a)"></div>
      <div class="date"><span class="month">MAY</span><span class="day">07</span></div>
      <h3 class="event-name">Copper Lantern Choir</h3>
    </article>
    <article class="event">
      <div class="event-photo" role="img" aria-label="Large arena crowd facing bright white stage lights" style="background:radial-gradient(ellipse at 50% 30%,#eef4ff,#4a6ac8 45%,#0a1030)"></div>
      <div class="date"><span class="month">MAY</span><span class="day">12</span></div>
      <h3 class="event-name">Rowan Tessely</h3>
    </article>
    <article class="event">
      <div class="event-photo" role="img" aria-label="Band silhouetted against colourful stage smoke" style="background:linear-gradient(120deg,#c82040,#3a9ae0 50%,#e8c040)"></div>
      <div class="date"><span class="month">MAY</span><span class="day">17</span></div>
      <h3 class="event-name">Delmar Hollow Band</h3>
    </article>
    <article class="event">
      <div class="event-photo" role="img" aria-label="Blurred crowd in front of a dim violet stage" style="background:linear-gradient(#6a6aa8,#2a2a4a 60%,#0a0a14)"></div>
      <div class="date"><span class="month">MAY</span><span class="day">20</span></div>
      <h3 class="event-name">Kairo Vance</h3>
    </article>
  </div>

  <footer class="footer">
    <div class="social" aria-label="Social links"><span></span><span></span><span></span></div>
    <ul class="footnav">
      <li>Home</li><li>How to order</li><li>About us</li><li>Contact us</li>
      <li>Policies</li><li>Privacy</li><li>Center sale</li><li>Access</li>
    </ul>
    <p class="copyright">© 2017 BROVLANEPASS.NET. ALL RIGHTS RESERVED.</p>
  </footer>
</div>
</body>
</html>
```